Financial Services General Marketing Brochure

Need a brochure to help recipients understand what makes BWC unique and the services that we offer. Must match look/feel of website https://brightwellcustody.example Layouts should make it easy to read the content - content should not be crammed into a traditional size/layout. Please see attached creative brief for specifics.

Target Market(s)

Financial advisors and mature couples looking for trustee services.

Industry/Entity Type

Financial Service

Colors
34a7d8
ffc214

Requirements
Must have
• See Creative Brief

```html
<!DOCTYPE html>
<html lang="en">
<head>
<meta charset="utf-8">
<title>Brightwell Custody Brochure</title>
<link href="https://fonts.googleapis.com/css2?family=Merriweather:ital,wght@0,400;0,700;1,400&family=Open+Sans:ital,wght@0,400;0,600;1,400&display=swap" rel="stylesheet">
<style>
  :root {
    --page-bg: #e4e4e4;
    --paper: #f7f7f5;
    --navy: #2c4869;
    --text: #55606b;
    --band: rgba(63, 110, 145, 0.88);
    --circle: #d5dde6;
    --accent: #f0a23a;
    --field-light: #ebe6d6;
    --field-dark: #cfc6a8;
    --grass: #7fa84a;
  }
  * { box-sizing: border-box; margin: 0; padding: 0; }
  html, body { width: 1200px; height: 1000px; overflow: hidden; }
  body { background: var(--page-bg); font-family: "Open Sans", sans-serif; color: var(--text); }

  .spread {
    position: absolute; left: 60px; top: 230px;
    width: 1080px; height: 540px; display: flex;
    box-shadow: 0 12px 30px rgba(0,0,0,0.18);
  }
  .panel { position: relative; width: 540px; height: 540px; overflow: hidden; background: var(--paper); }

  /* Back panel */
  .deco-circles { position: absolute; inset: 0; }
  .back-photo {
    position: absolute; left: 290px; top: 0; width: 250px; height: 195px;
    background: linear-gradient(135deg, #f1f1ef 0%, #c9cfd6 45%, #5b78a0 75%, #9fb4cf 100%);
  }
  .back-field {
    position: absolute; left: 0; top: 330px; width: 540px; height: 210px;
    background: linear-gradient(180deg, rgba(235,230,214,0) 0%, var(--field-light) 25%, var(--field-dark) 100%);
  }
  .info-col { position: absolute; left: 26px; top: 52px; width: 250px; }
  .specialties { position: absolute; left: 300px; top: 210px; width: 230px; }
  .section-title { font-family: "Merriweather", serif; font-weight: 700; color: var(--navy); font-size: 14px; line-height: 1.2; }
  .section-lead { font-style: italic; font-size: 9.5px; line-height: 1.35; margin: 2px 0 12px; }
  .plain-list { list-style: none; font-size: 9.5px; line-height: 1.4; margin: 3px 0 12px; }
  .bullet-list { font-size: 9.5px; line-height: 1.4; padding-left: 12px; }

  .back-contact { position: absolute; left: 250px; top: 370px; width: 260px; text-align: center; }
  .wordmark { display: inline-flex; align-items: center; gap: 8px; font-family: "Merriweather", serif; font-weight: 700; font-size: 19px; color: var(--navy); }
  .wordmark-dot { width: 16px; height: 16px; border-radius: 50%; background: var(--accent); }
  .contact-list { list-style: none; margin-top: 18px; font-size: 13px; line-height: 1.6; color: #4a4f55; }

  /* Front panel */
  .front-photo {
    position: absolute; left: 0; top: 0; width: 540px; height: 330px;
    background: linear-gradient(160deg, #9aa867 0%, #c7b98c 40%, #e7ddcb 65%, #b6bfa6 100%);
  }
  .front-grass {
    position: absolute; left: 0; top: 330px; width: 540px; height: 210px;
    background: linear-gradient(180deg, #a7b98a 0%, #6e9a3e 70%, var(--grass) 100%);
  }
  .front-band {
    position: absolute; left: 0; top: 320px; width: 540px; height: 150px;
    background: var(--band); display: flex; align-items: center; padding: 0 30px;
  }
  .tagline { font-family: "Merriweather", serif; color: #fff; font-size: 15px; line-height: 1.45; width: 280px; }
  .band-divider { width: 1px; height: 62px; background: rgba(255,255,255,0.7); margin: 0 24px; }
  .front-band .wordmark { color: #fff; font-size: 18px; }
</style>
</head>
<body>
  <main class="spread">
    <section class="panel back-panel">
      <div class="back-field" role="img" aria-label="Faded photo of a child and parent running across a sunlit field"></div>
      <svg class="deco-circles" width="540" height="540" viewBox="0 0 540 540" aria-hidden="true">
        <circle cx="300" cy="195" r="130" fill="var(--circle)" opacity="0.75"/>
        <circle cx="420" cy="250" r="95" fill="var(--circle)" opacity="0.6"/>
      </svg>
      <div class="back-photo" role="img" aria-label="Photo of a smiling mature couple meeting with an advisor"></div>

      <div class="info-col">
        <h2 class="section-title">What We Offer</h2>
        <p class="section-lead">We specialize exclusively in the delivery of trustee and estate fiduciary services.</p>
        <h2 class="section-title">Who We Serve</h2>
        <ul class="plain-list">
          <li>Families</li>
          <li>Professional Advisors</li>
          <li>Foundations</li>
        </ul>
        <h2 class="section-title">How We Serve</h2>
        <p class="section-lead">Our expertise and experience is in family wealth. In this regard, we serve in the following ways:</p>
        <ul class="bullet-list">
          <li>Trustee (Trusts)</li>
          <li>Executor and Personal Representative (Will)</li>
          <li>Agent for Financial Affairs (Power of Attorney)</li>
          <li>Trust Protector</li>
          <li>Special Independent Trustee</li>
          <li>Consultant</li>
          <li>Expert Witness</li>
        </ul>
      </div>

      <div class="specialties">
        <h2 class="section-title">Trust Specialties</h2>
        <p class="section-lead">The general types of trusts on which we serve as trustee:</p>
        <ul class="bullet-list">
          <li>Family Trusts</li>
          <li>Charitable Trusts</li>
          <li>Family Foundations</li>
          <li>Life Insurance Trusts</li>
          <li>Retirement Trusts</li>
          <li>Special Needs Trusts</li>
        </ul>
      </div>

      <div class="back-contact">
        <span class="wordmark"><span class="wordmark-dot"></span>Brightwell Custody</span>
        <ul class="contact-list">
          <li>brightwellcustody.example</li>
          <li>555-014-2290</li>
          <li>info@brightwellcustody.example</li>
        </ul>
      </div>
    </section>

    <section class="panel front-panel">
      <div class="front-photo" role="img" aria-label="Photo of a smiling three-generation family outdoors among trees"></div>
      <div class="front-grass" role="img" aria-label="Green meadow grass"></div>
      <div class="front-band">
        <p class="tagline">Helping families protect and enrich a multi-generational heritage</p>
        <span class="band-divider"></span>
        <span class="wordmark"><span class="wordmark-dot"></span>Brightwell Custody</span>
      </div>
    </section>
  </main>
</body>
</html>
```